New website: Wanderfjordia.com

We need to build a website for our small travel agency.
We want to be able to upload our brochures and offer our tours on site. No online payments involved yet.

We want to create an exact copy of another website: www.trekvalora.is, but with our own information and products. We like that design very much.

We are not going to do any sales via the website as the website above, but instead we want to show in the same style and everything the different tours that we offer.

We need to be able to modify tours: tour pictures, info, add videos, text, etc.

We need the website in English and Spanish. We can provide the Spanish translation.

We would advice you to create a copy of that website, with the text to be editable by us.
We own the website www.wanderfjordia.com and need that the designer uploads it and makes it work as well.

We have uploaded some pictures that can be used as place markers.

I HAVE UPLOADED OUR BROCHURE DEMO SO YOU CAN GET MORE INFO IN ENGLISH ABOUT US AND MORE PICTURES.

PLEASE REMEMBER THAT THE WEBSITE ¨MOVES¨ when you resize it! Specially the pictures get ¨bigger¨ or smaller¨ when you resize. The same applies to the logos :-)

Once you have created the front page just as the original website I will select it and then we can put the real info and extra pages :-)

Tourists, international people traveling.

Tourism

Coded - Design and coding required

5+ page

Sans Serif

ffffff

• Exactly the same layout of the website mentioned (www.trekvalora.is)
• Everything the same, but with our own logo, texts and photos.
• HOME
• TOURS
• GROUPS
• OUR MOST POPULAR TOURS

```html
<!DOCTYPE html>
<html lang="en">
<head>
<meta charset="utf-8">
<title>Wanderfjordia – Home</title>
<link href="https://fonts.googleapis.com/css2?family=Exo+2:wght@400;500;600&family=Open+Sans:wght@400;600&display=swap" rel="stylesheet">
<style>
:root{
  --red:#e0262b;
  --ink:#222226;
  --muted:#7a7a80;
  --price:#2c7fd0;
  --band:#efeff3;
  --line:#e3e3e6;
  --footer:#050505;
  --white:#ffffff;
}
*{margin:0;padding:0;box-sizing:border-box}
html,body{width:1200px;height:3390px;overflow:hidden;background:var(--white)}
body{position:relative;font-family:"Open Sans",Arial,sans-serif;color:var(--ink)}
.abs{position:absolute}
.head-font{font-family:"Exo 2",Arial,sans-serif}

/* header */
.site-header{position:absolute;left:0;top:0;width:1200px;height:105px;background:var(--white)}
.brand{position:absolute;left:112px;top:8px;width:126px;height:126px;border-radius:50%;background:#0c0c0c;border:4px solid var(--white);box-shadow:0 2px 6px rgba(0,0,0,.25);display:flex;align-items:center;justify-content:center;z-index:5}
.brand span{font-family:"Exo 2",sans-serif;font-weight:600;color:var(--white);font-size:15px;letter-spacing:.5px}
.main-nav a{position:absolute;top:45px;font-family:"Exo 2",sans-serif;font-weight:500;font-size:13px;color:var(--ink);text-decoration:none;letter-spacing:.3px}
.main-nav a.active{color:var(--red)}
.lang{position:absolute;top:45px;width:24px;height:15px}

/* hero */
.hero{position:absolute;left:0;top:105px;width:1200px;height:475px;background:var(--white)}
.hero-panel{position:absolute;left:0;top:0;width:1200px;height:475px}
.hero-main{clip-path:polygon(0 0,712px 0,600px 475px,0 475px);background:linear-gradient(180deg,#6c9ac7 0%,#a9c3dc 32%,#8b98a8 50%,#3f5568 62%,#1f3a55 80%,#142a40 100%)}
.hero-top{clip-path:polygon(719px 0,1200px 0,1200px 235px,662px 235px);background:linear-gradient(180deg,#5f7184 0%,#9aa6b2 45%,#5a6470 70%,#2c3238 100%)}
.hero-bottom{clip-path:polygon(660px 242px,1200px 242px,1200px 475px,604px 475px);background:linear-gradient(180deg,#6a7a8c 0%,#a3acb5 40%,#4d5864 75%,#262d34 100%)}
.hero-caption{position:absolute;font-family:"Exo 2",sans-serif;font-size:20px;color:var(--white);text-shadow:0 1px 3px rgba(0,0,0,.6)}
.hero-caption svg{vertical-align:-2px;margin-left:4px}

/* tours */
.section-title{position:absolute;left:0;width:1200px;text-align:center;font-family:"Exo 2",sans-serif;font-weight:500;font-size:25px;color:var(--ink);letter-spacing:.3px}
.tabs{position:absolute;left:110px;top:700px;width:980px;height:42px;border-bottom:1px solid var(--line)}
.tabs a{position:absolute;top:0;font-size:13px;color:var(--ink);text-decoration:none;white-space:nowrap}
.tabs a.active{color:var(--red);padding-bottom:13px;border-bottom:3px solid var(--red)}
.tour{position:absolute;width:310px}
.tour .photo{width:310px;height:215px;box-shadow:0 12px 12px -10px rgba(0,0,0,.35)}
.tour h3{margin-top:33px;font-family:"Exo 2",sans-serif;font-weight:400;font-size:16px;color:var(--ink)}
.tour .length{margin-top:12px;font-size:12px;color:var(--muted)}
.tour .price{margin-top:11px;font-family:"Exo 2",sans-serif;font-size:16px;color:var(--price)}
.btn{position:absolute;display:flex;align-items:center;justify-content:center;border:2px solid var(--red);color:var(--red);font-family:"Exo 2",sans-serif;font-size:16px;text-decoration:none;border-radius:3px;box-shadow:0 3px 6px rgba(0,0,0,.12);background:var(--white)}

/* info bands */
.band{position:absolute;left:0;width:1200px;background:var(--band)}
.h2{position:absolute;font-family:"Exo 2",sans-serif;font-weight:500;font-size:24px;color:var(--ink);letter-spacing:.5px}
.copy{position:absolute;font-size:11.5px;line-height:30px;color:#55555b;text-align:justify}
.illus{position:absolute}

/* footer */
.site-footer{position:absolute;left:0;top:3141px;width:1200px;height:249px;background:var(--footer);color:var(--white)}
.foot-brand{position:absolute;left:117px;top:37px;width:116px;height:116px;border-radius:50%;background:#000;border:3px solid var(--white);display:flex;align-items:center;justify-content:center}
.foot-brand span{font-family:"Exo 2",sans-serif;font-weight:600;font-size:14px;color:var(--white)}
.foot-links{position:absolute;list-style:none}
.foot-links li{font-size:11.5px;height:30.5px;line-height:20px}
.foot-title{position:absolute;top:38px;font-family:"Exo 2",sans-serif;font-size:18px;letter-spacing:.8px}
.contact-list{position:absolute;left:667px;top:80px;list-style:none}
.contact-list li{font-size:11.5px;height:31.5px;display:flex;align-items:center;gap:10px}
.social-list{position:absolute;left:960px;top:77px;list-style:none}
.social-list li{font-size:11px;height:28.5px;display:flex;align-items:center;gap:8px}
.social-list i{display:inline-block;width:13px;height:13px;background:#5b6b85}
.page-no{position:absolute;right:18px;bottom:10px;font-size:10px;color:#ccc}
</style>
</head>
<body>

<header class="site-header">
  <div class="brand"><span>Wanderfjordia</span></div>
  <nav class="main-nav">
    <a class="active" style="left:416px">HOME</a>
    <a style="left:505px">TOURS</a>
    <a style="left:598px">GROUPS</a>
    <a style="left:700px">RENT A CAR</a>
    <a style="left:824px">FLIGHT</a>
    <a style="left:916px">CONTACT</a>
  </nav>
  <svg class="lang" style="left:1000px" viewBox="0 0 24 15" aria-label="Español"><rect width="24" height="15" fill="#c60b1e"/><rect y="4" width="24" height="7" fill="#ffc400"/></svg>
  <svg class="lang" style="left:1036px" viewBox="0 0 24 15" aria-label="English"><rect width="24" height="15" fill="#012169"/><path d="M0 0L24 15M24 0L0 15" stroke="#fff" stroke-width="3"/><path d="M12 0V15M0 7.5H24" stroke="#fff" stroke-width="5"/><path d="M12 0V15M0 7.5H24" stroke="#c8102e" stroke-width="3"/></svg>
</header>

<section class="hero">
  <div class="hero-panel hero-main" role="img" aria-label="Lake and snowy granite peaks under a cloudy blue sky"></div>
  <div class="hero-panel hero-top" role="img" aria-label="Windswept valley with dark mountains and clouds"></div>
  <div class="hero-panel hero-bottom" role="img" aria-label="Mountain range under heavy clouds"></div>
  <div class="hero-caption" style="left:52px;top:420px">Outdoor adventures in El Chaltén<svg width="14" height="14" viewBox="0 0 14 14"><path d="M0 7H10M6 2L11 7L6 12" stroke="#fff" stroke-width="2.4" fill="none"/></svg></div>
  <div class="hero-caption" style="left:708px;top:186px">Walk with the pre-historic<svg width="14" height="14" viewBox="0 0 14 14"><path d="M0 7H10M6 2L11 7L6 12" stroke="#fff" stroke-width="2.4" fill="none"/></svg></div>
  <div class="hero-caption" style="left:649px;top:425px">Penguin-watch at Punta Tombo<svg width="14" height="14" viewBox="0 0 14 14"><path d="M0 7H10M6 2L11 7L6 12" stroke="#fff" stroke-width="2.4" fill="none"/></svg></div>
</section>

<h2 class="section-title" style="top:643px">OUR MOST POPULAR TOURS</h2>
<nav class="tabs">
  <a class="active" style="left:22px">Popular Tours</a>
  <a style="left:160px">Day Tours</a>
  <a style="left:270px">Travel by Air Tours</a>
  <a style="left:438px">Self Drive Tours</a>
  <a style="left:585px">Adventures Tours</a>
  <a style="left:746px">Customize Tours</a>
  <a style="left:900px">Transfer</a>
</nav>

<article class="tour" style="left:110px;top:791px">
  <div class="photo" role="img" aria-label="Green northern lights over a snowy plain" style="background:linear-gradient(180deg,#0c1a22 0%,#2d6b52 40%,#4d8a78 55%,#1a2a33 75%,#cfd8dc 100%)"></div>
  <h3>Explore Cueva de las Manos</h3><p class="length">length: 3 - 5 hours</p><p class="price">8,800 ISK</p>
</article>
<article class="tour" style="left:445px;top:791px">
  <div class="photo" role="img" aria-label="Path through a grassy lava canyon" style="background:linear-gradient(180deg,#dfe6ea 0%,#b8c6cc 30%,#5c5a4e 55%,#6f8a45 80%,#8a8a80 100%)"></div>
  <h3>Dive into watersports</h3><p class="length">length: 3 - 5 hours</p><p class="price">8,800 ISK</p>
</article>
<article class="tour" style="left:780px;top:791px">
  <div class="photo" role="img" aria-label="Blue-lit ice tunnel" style="background:linear-gradient(180deg,#2a2fb0 0%,#4a4ee0 45%,#8f7ff0 70%,#2a2690 100%)"></div>
  <h3>Explore Cueva de las Manos</h3><p class="length">length: 3 - 5 hours</p><p class="price">8,800 ISK</p>
</article>
<article class="tour" style="left:110px;top:1160px">
  <div class="photo" role="img" aria-label="Rainbow over misty mountains" style="background:linear-gradient(180deg,#8e9aa6 0%,#b9c1c8 45%,#6b747c 75%,#3d4348 100%)"></div>
  <h3>Volcanoes &amp; Glaciers from up above</h3><p class="length">length: 3 - 5 hours</p><p class="price">135.900 ISK</p>
</article>
<article class="tour" style="left:445px;top:1160px">
  <div class="photo" role="img" aria-label="Frozen waterfall among snow and ice" style="background:linear-gradient(180deg,#1f3f70 0%,#dce6ef 35%,#2b4a6e 60%,#e8eef4 100%)"></div>
  <h3>Essential Iceland</h3><p class="length">length: 3 - 5 hours</p><p class="price">42.900 ISK</p>
</article>
<article class="tour" style="left:780px;top:1160px">
  <div class="photo" role="img" aria-label="Orcas surfacing in blue sea" style="background:linear-gradient(180deg,#1d5ea0 0%,#2a72b8 50%,#1b4f86 100%)"></div>
  <h3>Whale Watching</h3><p class="length">length: 3 - 5 hours</p><p class="price">8,800 ISK</p>
</article>

<a class="btn" style="left:461px;top:1539px;width:278px;height:61px">VIEW ALL OUR POPULAR TOUR</a>

<section class="band" style="top:1648px;height:232px">
  <h2 class="section-title" style="top:64px;font-size:24px">WELCOME</h2>
  <p class="copy" style="left:190px;top:109px;width:820px;text-align:center;line-height:29px">Wanderfjordia es un nuevo tour operator receptivo de confianza especializado en el diseño y prestación de servicios personalizados de incoming<br>en destinos prístinos de la Ecorregión Sub-Antártica y Antártica Chilena.</p>
</section>

<section>
  <div class="illus" role="img" aria-label="Stack of suitcases with beach gear, hats and a surfboard" style="left:34px;top:1940px;width:306px;height:320px;background:radial-gradient(ellipse at 50% 55%,#d9a06a 0%,#c98a4a 35%,#e9e2d8 65%,#ffffff 78%)"></div>
  <h2 class="h2" style="left:375px;top:1988px">QUIENES SOMOS</h2>
  <p class="copy" style="left:376px;top:2040px;width:710px">Somos una empresa conformada por un idóneo equipo de trabajo que consta de alta motivación, óptimo entrenamiento, elevado capital humano y cuyos integrantes poseen más de 10 años de experiencia trabajando en forma independiente en Turismo Receptivo Regional, Nacional e Internacional. En conjunto nos potenciamos y logramos satisfacer las altas demandas de servicios turísticos requeridos por nuestros clientes.</p>
  <a class="btn" style="left:382px;top:2177px;width:158px;height:56px;font-size:15px">CONTACT US</a>
</section>

<section class="band" style="top:2321px;height:391px">
  <h2 class="h2" style="left:113px;top:106px">MISION</h2>
  <p class="copy" style="left:113px;top:140px;width:682px">Nuestra misión es ofrecer servicios de Turismo Receptivo para la Región de Magallanes y Antártica Chilena que cumplan con las exigencias de calidad y valor humano que nuestros clientes solicitan. Para lograrlo, trabajamos en conjunto con proveedores turísticos seleccionados y nos enfocamos hacia la excelencia de un servicio personalizado, sirviendo con pasión, experiencia y responsabilidad a cada uno de nuestros clientes.</p>
  <div class="illus" role="img" aria-label="Globe topped with world landmarks and a plane" style="left:825px;top:52px;width:282px;height:271px;background:radial-gradient(circle at 50% 62%,#3a8fd8 0%,#7bb8ea 40%,#d8dde4 62%,rgba(239,239,243,0) 72%)"></div>
</section>

<section>
  <div class="illus" role="img" aria-label="Colourful suitcases, passports and a map" style="left:79px;top:2791px;width:283px;height:271px;background:radial-gradient(circle at 40% 40%,#bfe3ee 0%,#8fc9dc 40%,#f08a3a 62%,#ffffff 76%)"></div>
  <h2 class="h2" style="left:407px;top:2825px">VISION</h2>
  <p class="copy" style="left:407px;top:2870px;width:712px">Nuestra visión es crear una Plataforma de Servicios Logísticos y Turísticos para la Ecorregión Sub-Antártica y Antártica que una toda la oferta turística de la zona a través de una red local, nacional y global de proveedores, con el objetivo de mejorar, a través de la cuidadosa selección de prestadores, la accesibilidad por parte del cliente, la competitividad dentro del mercado, facilitando la inclusión de pequeñas y medianas empresas.</p>
  <a class="btn" style="left:409px;top:3008px;width:161px;height:57px;font-size:15px">READ MORE</a>
</section>

<footer class="site-footer">
  <div class="foot-brand"><span>Wanderfjordia</span></div>
  <ul class="foot-links" style="left:350px;top:40px">
    <li>Home</li><li>Tours</li><li>Groups</li><li>Rent a Car</li><li>Flight</li><li>Contact</li>
  </ul>
  <ul class="foot-links" style="left:488px;top:40px">
    <li>How To Book</li><li>Booking Terms</li><li>Privacy Policy</li><li>Sitemap</li>
  </ul>
  <h4 class="foot-title" style="left:667px">CONTACT US</h4>
  <ul class="contact-list">
    <li><svg width="12" height="14" viewBox="0 0 12 14"><path d="M6 0C2.7 0 0 2.6 0 5.8 0 10 6 14 6 14s6-4 6-8.2C12 2.6 9.3 0 6 0z" fill="#7d7d7d"/><circle cx="6" cy="5.6" r="2.2" fill="#050505"/></svg>123, Lorm Ipsm, Lorem Ipsm - 123 456</li>
    <li><svg width="14" height="14" viewBox="0 0 14 14"><rect width="14" height="14" rx="2" fill="var(--red)"/><path d="M4 3.5c.5-.5 1.2-.4 1.5.2l.6 1.2c.2.4 0 .8-.3 1-.3.3-.3.6 0 1l1.3 1.3c.4.3.7.3 1 0 .2-.3.6-.5 1-.3l1.2.6c.6.3.7 1 .2 1.5-1 1-2.7.9-4.8-1.2S3 4.5 4 3.5z" fill="#fff"/></svg>08-512-7790</li>
    <li><svg width="14" height="14" viewBox="0 0 14 14"><rect width="14" height="14" rx="2" fill="var(--red)"/><rect x="3" y="5" width="8" height="5" fill="#fff"/><rect x="4.5" y="3" width="5" height="2" fill="#fff"/></svg>08-512-7790</li>
    <li><svg width="14" height="14" viewBox="0 0 14 14"><rect width="14" height="14" rx="2" fill="var(--red)"/><rect x="3" y="4" width="8" height="6" fill="#fff"/><path d="M3 4L7 7.5L11 4" stroke="var(--red)" stroke-width="1" fill="none"/></svg>info@wanderfjordia.com</li>
  </ul>
  <h4 class="foot-title" style="left:960px">CONNECT US</h4>
  <ul class="social-list">
    <li><i></i>Friendwall</li>
    <li><i style="background:#4d8fc8"></i>Chirpline</li>
    <li><i style="background:#3f6fa3"></i>Workchain</li>
    <li><i style="background:#c9473a"></i>Circleplus</li>
    <li><i style="background:#e08a2a"></i>RSS</li>
  </ul>
  <span class="page-no">C10</span>
</footer>

</body>
</html>
```